Redesign Of Current Landing Page

I need to redesign this landing page https://www.brightlanepromo.biz/?page=landing&landing=23 (Please do not opt in because when you do it will show you the home page. Please clear your cookies before going to this url above to view the 1 page landing page.)

Please use my updated website as a reference for colors and logo.
http://sitecradlewerk.com/dh/bpq/index.html

I would like the call to action to be a button that opens into a lead form...

Button would be "Download Samples"

Target Market(s)

small business owners

Industry/Entity Type

Marketing

Number of Pages Required

1 page

Colors

Designer to choose colors to be used in the design.

Requirements
Must have
• must be full responsive on all devices
Nice to have
• must have a legitimate professional apeal to it
Should not have
• open

```html
<!DOCTYPE html>
<html lang="en">
<head>
<meta charset="utf-8">
<title>Bright Lane Promotions Group – Landing</title>
<link href="https://fonts.googleapis.com/css2?family=Merriweather:wght@400;700&family=Poppins:wght@400;500;600&display=swap" rel="stylesheet">
<style>
:root{
  --blue:#1b6fc2;
  --blue-btn:#1478cc;
  --orange:#ffa800;
  --orange-soft:#f7c27a;
  --tile:#f4f4f4;
  --card:#f6f7f6;
  --text:#6a6a6a;
  --dark:#333;
  --rule:#9a9a9a;
  --footer:#232323;
}
*{margin:0;padding:0;box-sizing:border-box}
html,body{width:754px;height:1200px;overflow:hidden;background:#fff}
body{position:relative;font-family:'Poppins',sans-serif;color:var(--text)}
.abs{position:absolute}
.serif{font-family:'Merriweather',serif}

.site-header{left:0;top:0;width:754px;height:35px;background:#fff}
.brand{left:62px;top:10px;font-family:'Poppins',sans-serif;font-weight:500;font-size:12px;line-height:15px;color:var(--dark)}
.nav{right:63px;top:12px;display:flex;gap:27px;font-size:8px;color:#444}

.hero{left:0;top:35px;width:754px;height:286px;background:linear-gradient(135deg,#3a3633,#5b554f 45%,#2f2c2a)}
.hero-title{left:0;width:754px;text-align:center;color:#fff}
.hero-title.h1{top:117px;font-size:22.5px;font-weight:700}
.hero-title.h2{top:160px;font-size:19px;line-height:30px;font-weight:400}
.btn-hero{left:303px;top:228px;width:152px;height:29px;background:var(--blue-btn);color:#fff;font-size:14px;text-align:center;line-height:29px}

.center{left:0;width:754px;text-align:center}
.why-title{top:337px;font-size:17px;font-weight:700;color:var(--blue)}
.lead{top:367px;left:125px;width:504px;font-size:6.4px;line-height:13px;text-align:center}

.tile{top:404px;width:150px;height:110px;background:var(--tile);text-align:center;font-size:8.5px;line-height:14px;color:#777;letter-spacing:.3px}
.tile svg{position:absolute;left:58px;top:22px}
.tile p{position:absolute;left:10px;right:10px;top:64px}
.tile.active{background:var(--orange);color:#fff;font-weight:500}

.rule{left:62px;width:630px;height:1px;background:var(--rule)}
.label{height:20px;border:1px solid #777;background:#fff;color:var(--blue);font-size:12px;text-align:center;line-height:18px}
.body-text{left:85px;width:584px;font-size:6.4px;line-height:13px;text-align:justify;text-align-last:center}
.btn-orange{background:var(--orange);color:#fff;text-align:center}

.card{top:877px;width:173px;height:199px;background:var(--card)}
.card svg{position:absolute;left:74px;top:24px}
.card p{position:absolute;left:21px;right:21px;top:57px;font-size:6.3px;line-height:13px;text-align:justify;text-align-last:center}
.avatar{width:55px;height:55px;border-radius:50%;border:2px solid var(--orange);background:linear-gradient(#d8cfc6,#b9a999)}
.person{width:200px;text-align:center;color:#444;font-size:10px;line-height:17px}

.site-footer{left:0;top:1166px;width:754px;height:34px;background:var(--footer);color:#fff;font-size:7.5px;text-align:center;line-height:34px}
</style>
</head>
<body>
<header class="site-header abs">
  <div class="brand abs">Bright Lane Promotions</div>
  <nav class="nav abs"><span>Home</span><span>About Us</span><span>Testimonials</span><span>Samples</span><span>FAQ</span><span>Contact</span></nav>
</header>

<section class="hero abs" role="img" aria-label="Overhead photo of a team meeting around a table with laptops and papers"></section>
<h1 class="hero-title h1 abs serif">ATTRACT MORE CUSTOMERS</h1>
<h2 class="hero-title h2 abs serif">Who Spend More Money With Your<br>Business More Often!</h2>
<div class="btn-hero abs serif">Download Samples</div>

<h2 class="why-title center abs serif">Why Offer Incentives To Customers?</h2>
<p class="lead abs">Bright Lane Promotions Group, Inc. provides high-perceived value promotional incentives to businesses that want to advertise an exciting Give Away that will instantly attract more customers from your existing advertising efforts.</p>

<div class="tile abs" style="left:62px">
  <svg width="34" height="26" viewBox="0 0 34 26"><path d="M1 0v25h32" fill="none" stroke="#1b6fc2" stroke-width="2"/><rect x="6" y="13" width="4" height="10" fill="#1b6fc2"/><rect x="12" y="8" width="4" height="15" fill="#1b6fc2"/><rect x="18" y="11" width="4" height="12" fill="#1b6fc2"/><rect x="24" y="4" width="4" height="19" fill="#1b6fc2"/></svg>
  <p>Increase Responses From Your Existing Ads</p>
</div>
<div class="tile abs" style="left:222px">
  <svg width="34" height="28" viewBox="0 0 34 28"><circle cx="12" cy="14" r="8" fill="none" stroke="#1b6fc2" stroke-width="5" stroke-dasharray="3 2.3"/><circle cx="12" cy="14" r="3" fill="#1b6fc2"/><circle cx="27" cy="7" r="4.5" fill="none" stroke="#1b6fc2" stroke-width="3.5" stroke-dasharray="2 1.6"/><circle cx="27" cy="22" r="4.5" fill="none" stroke="#1b6fc2" stroke-width="3.5" stroke-dasharray="2 1.6"/></svg>
  <p>Insure The Sale Over Your Competition</p>
</div>
<div class="tile active abs" style="left:382px">
  <svg width="34" height="30" viewBox="0 0 34 30"><path d="M3 14L31 2 24 28 15 19zM15 19l16-17" fill="none" stroke="#fff" stroke-width="2" stroke-linejoin="round"/></svg>
  <p style="top:67px">Build Brand Awareness and Trust</p>
</div>
<div class="tile abs" style="left:542px">
  <svg width="34" height="30" viewBox="0 0 34 30"><rect x="6" y="4" width="10" height="14" transform="rotate(-45 11 11)" fill="#1b6fc2"/><path d="M15 15l14 12" stroke="#1b6fc2" stroke-width="4" stroke-linecap="round"/></svg>
  <p>Boost Repeat and Referral Business</p>
</div>

<div class="rule abs" style="top:557px"></div>
<div class="label abs serif" style="left:327px;top:548px;width:99px">Imagine</div>
<p class="body-text abs" style="top:585px">Being able to create exciting give away promotions that will boost your sales without ever having to worry about cost. Bright Lane Promotions Group, Inc. provides high-perceived value promotional incentives to businesses that want to advertise an exciting Give Away that will instantly attract more customers from your existing advertising efforts. Your business can give away incentive certificates that are redeemable for luxury hotel &amp; resort stays with airfare.</p>
<div class="btn-orange abs serif" style="left:331px;top:636px;width:86px;height:22px;line-height:22px;font-size:9.5px;font-weight:700">Read More</div>

<div class="rule abs" style="top:697px"></div>
<div class="label abs serif" style="left:307px;top:685px;width:139px;height:23px;line-height:21px">How Can We Do It?</div>
<p class="body-text abs" style="top:727px">We help fill empty rooms for thousands of hotels and resorts in hundreds of destinations around the world as well as the major cruise lines. Hotels and resorts are rarely full so when we place someone in their empty rooms, they end up making it up when travelers spend money on room service, spa services, eat at their in-house restaurants, casino and take advantage of other amenities that drive revenue.</p>
<div class="btn-orange abs" style="left:300px;top:780px;width:150px;height:22px;line-height:22px;font-size:7.5px;font-weight:600">REQUEST FREE SAMPLE PACKAGE</div>

<div class="rule abs" style="top:839px"></div>
<div class="label abs serif" style="left:307px;top:827px;width:139px;height:23px;line-height:21px">Testimonials</div>

<div class="card abs" style="left:92px">
  <svg width="24" height="18" viewBox="0 0 24 18"><path d="M1 18V9q0-8 9-9v4q-4 1-4 5h4v9zM14 18V9q0-8 9-9v4q-4 1-4 5h4v9z" fill="var(--orange-soft)"/></svg>
  <p>I began using your incentives two years ago to boost lead generation efforts. I have experienced a 63% increase in lead captures. And, even more importantly, my sales have increased as well. The ability to offer unlimited certificates and not having.</p>
</div>
<div class="card abs" style="left:289px">
  <svg width="24" height="18" viewBox="0 0 24 18"><path d="M1 18V9q0-8 9-9v4q-4 1-4 5h4v9zM14 18V9q0-8 9-9v4q-4 1-4 5h4v9z" fill="var(--orange-soft)"/></svg>
  <p>Lorem Ipsum is simply dummy text of the printing and typesetting industry. Lorem Ipsum has been the industry's standard dummy text ever since the 1500s, when an unknown printer took a galley of type and scrambled it to make a type specimen book.</p>
</div>
<div class="card abs" style="left:489px">
  <svg width="24" height="18" viewBox="0 0 24 18"><path d="M1 18V9q0-8 9-9v4q-4 1-4 5h4v9zM14 18V9q0-8 9-9v4q-4 1-4 5h4v9z" fill="var(--orange-soft)"/></svg>
  <p>Lorem Ipsum is simply dummy text of the printing and typesetting industry. Lorem Ipsum has been the industry's standard dummy text ever since the 1500s, when an unknown printer took a galley of type and scrambled it to make a type specimen book.</p>
</div>

<div class="avatar abs" style="left:146px;top:1050px" role="img" aria-label="Portrait of client Ray T."></div>
<div class="avatar abs" style="left:345px;top:1050px" role="img" aria-label="Portrait of client Nina Foster"></div>
<div class="avatar abs" style="left:547px;top:1051px" role="img" aria-label="Portrait of client Claire"></div>

<div class="person abs serif" style="left:73px;top:1110px">Ray T.<br>Oakfield, TN</div>
<div class="person abs serif" style="left:273px;top:1110px">Nina Foster<br>Oakfield, TN</div>
<div class="person abs serif" style="left:474px;top:1111px">Claire<br>Oakfield, TN</div>

<footer class="site-footer abs">Copyright 2017 Bright Lane Promotions Group, Inc. All rights reserved.</footer>
</body>
</html>
```